Aerial Imaging and photgraphy business card

Design a business card with eye catching aerial photo of country side / landscape with a drone in the foreground.
Also contact details.

Target Market(s)

Aerial Imaging photography

Industry/Entity Type

Advertising

Contact Information for Business Card

Rowland
0412965203
Website http://www.skywardvistaphoto.com.au/
email address : skywardvistaphoto.com.au

Colors
e8f1ca
cadf82
9bcb3c
33a6d7
85cae6
cee9f5

Requirements
Must have
• High res photo
• Korvane drone in the foreground Either T4200 and korvane Glidewing or both
Nice to have
• high resolution landscape country photo on the front of the card with a Korvane T4200 drone in the foreground.

```html
<!DOCTYPE html>
<html lang="en">
<head>
<meta charset="utf-8">
<title>Skyward Vista Imaging – Business Card</title>
<link href="https://fonts.googleapis.com/css2?family=Arimo:wght@400;700&display=swap" rel="stylesheet">
<style>
  :root {
    --page-bg: #e9e6e1;
    --card-bg: #ffffff;
    --sky-top: #8f95d6;
    --sky-mid: #7d86c9;
    --hill-violet: #6f6fb6;
    --hill-green: #7fa06a;
    --icon-blue: #33a6d7;
    --ink: #1e1e1e;
    --ink-soft: #5a5a5a;
    --brand-ink: #2f3136;
    --brand-dot: #9bcb3c;
  }
  * { box-sizing: border-box; margin: 0; padding: 0; }
  html, body { width: 1200px; height: 902px; overflow: hidden; }
  body {
    background: var(--page-bg);
    font-family: "Arimo", Arial, sans-serif;
    position: relative;
  }
  .business-card {
    position: absolute;
    left: 100px; top: 165px;
    width: 1000px; height: 572px;
    background: var(--card-bg);
    overflow: hidden;
    box-shadow: 0 6px 24px rgba(0,0,0,0.18);
  }
  .landscape-photo {
    position: absolute; left: 0; top: 0;
    width: 100%; height: 390px;
    background:
      linear-gradient(180deg, rgba(255,255,255,0) 72%, #ffffff 100%),
      linear-gradient(160deg, var(--sky-top) 0%, var(--sky-mid) 28%, var(--hill-violet) 48%, var(--hill-green) 78%, #a9c08f 100%);
  }
  .brand {
    position: absolute; left: 270px; top: 120px;
    display: flex; align-items: center; gap: 14px;
  }
  .brand-dot {
    width: 30px; height: 30px; border-radius: 50%;
    background: var(--brand-dot);
  }
  .brand-name {
    font-weight: 700; font-size: 40px; color: var(--brand-ink);
    letter-spacing: 0.5px;
  }
  .contact-list {
    position: absolute; right: 40px; top: 250px;
    list-style: none;
    display: flex; flex-direction: column; gap: 14px;
  }
  .contact-item {
    display: flex; align-items: center; justify-content: flex-end; gap: 14px;
    font-size: 24px; color: var(--ink);
  }
  .contact-icon {
    width: 30px; height: 30px; background: var(--icon-blue);
    display: flex; align-items: center; justify-content: center;
    border-radius: 3px;
  }
  .contact-icon svg { width: 20px; height: 20px; }
  .person {
    position: absolute; left: 60px; top: 448px;
  }
  .person-name { font-weight: 700; font-size: 32px; color: var(--ink); }
  .person-role { font-size: 24px; color: var(--ink-soft); margin-top: 4px; margin-left: 10px; }
</style>
</head>
<body>
  <article class="business-card">
    <div class="landscape-photo" role="img" aria-label="Aerial photo of a green coastal mountain landscape with a drone flying in the foreground"></div>

    <div class="brand">
      <span class="brand-dot"></span>
      <span class="brand-name">SKYWARD VISTA IMAGING</span>
    </div>

    <ul class="contact-list">
      <li class="contact-item">
        <span>0412965203</span>
        <span class="contact-icon"><svg viewBox="0 0 20 20"><path d="M5 2 L8 2 L9 6 L7 8 C8 10.5 9.5 12 12 13 L14 11 L18 12 L18 15 C18 16.5 16.5 18 15 18 C8 17 3 12 2 5 C2 3.5 3.5 2 5 2 Z" fill="#fff"/></svg></span>
      </li>
      <li class="contact-item">
        <span>info@skywardvista.com</span>
        <span class="contact-icon"><svg viewBox="0 0 20 20"><rect x="2" y="5" width="16" height="11" fill="#fff"/><path d="M2 5 L10 11 L18 5" fill="none" stroke="#33a6d7" stroke-width="1.5"/></svg></span>
      </li>
      <li class="contact-item">
        <span>www.skywardvistaphoto.com.au</span>
        <span class="contact-icon"><svg viewBox="0 0 20 20"><circle cx="10" cy="10" r="7.5" fill="none" stroke="#fff" stroke-width="1.6"/><ellipse cx="10" cy="10" rx="3.2" ry="7.5" fill="none" stroke="#fff" stroke-width="1.4"/><line x1="2.5" y1="10" x2="17.5" y2="10" stroke="#fff" stroke-width="1.4"/></svg></span>
      </li>
      <li class="contact-item">
        <span>Bellfield NSW 2587, Australia</span>
        <span class="contact-icon"><svg viewBox="0 0 20 20"><path d="M10 2 C6.5 2 4.5 4.5 4.5 7.5 C4.5 11.5 10 18 10 18 C10 18 15.5 11.5 15.5 7.5 C15.5 4.5 13.5 2 10 2 Z" fill="#fff"/><circle cx="10" cy="7.5" r="2.2" fill="#33a6d7"/></svg></span>
      </li>
    </ul>

    <div class="person">
      <p class="person-name">Martin Hale</p>
      <p class="person-role">Owner</p>
    </div>
  </article>
</body>
</html>
```